TL - business card

Tallow Partners is an insurance brokerage firm, inovative, proactive, vigorous, which aims to become the leader of the insurance brokers in Anfrica. We should like to get some designs which should be avoided also in Gray / Metallic for the Administration and Orange / Blue for the Managers (ike in the picture sent). The Blue / Green logo is not the correct one, but the source of the file. Please adjust the color accordingly for the business cards. 1 / Orange / Blue 2 / Gray / Metallic We want something classic but which is transmitted strenght, inovation, modernity and most of all, rapidity. We want something start-up like, very punchy and catching eye remaining profesional at the same time. Name: Dorian Whitlock Function: Managing Director Address: N ° 17/18 Rua Veloso - R / C 2B Direita - Bairro Mutamba - Luanda Tel: (+244) 947 582 316 Email: dorian.whitlock@tallow-p.example Website: www.tallow-p. example We want classic in the front and creative, colorfull at the back. The cards will be printed in relief, with very high quality of paper.
Insurance Broker
Colors
Designer to choose colors to be used in the design.

```html
<!DOCTYPE html>
<html lang="en">
<head>
<meta charset="utf-8">
<title>Tallow Partners – Business Card</title>
<link href="https://fonts.googleapis.com/css2?family=Ubuntu:wght@400;500;700&display=swap" rel="stylesheet">
<style>
  :root {
    --backdrop: #d9d6d2;
    --metal-dark: #1f2226;
    --metal-mid: #3b4047;
    --metal-light: #6b717a;
    --metal-sheen: #8d939b;
    --accent-orange: #f28c28;
    --accent-blue: #3a9bdc;
    --text-light: #f1f2f4;
    --text-muted: #cfd3d8;
  }
  * { margin: 0; padding: 0; box-sizing: border-box; }
  html, body { width: 1200px; height: 913px; overflow: hidden; }
  body {
    background: var(--backdrop);
    font-family: "Ubuntu", sans-serif;
    position: relative;
  }
  .card {
    position: absolute;
    top: 302px;
    width: 540px;
    height: 309px;
    border-radius: 4px;
    overflow: hidden;
    box-shadow: 0 14px 30px rgba(0,0,0,0.28);
  }
  .card-surface {
    position: absolute; inset: 0;
    background:
      linear-gradient(150deg, var(--metal-mid) 0%, var(--metal-dark) 38%, var(--metal-light) 62%, var(--metal-sheen) 68%, var(--metal-mid) 80%, var(--metal-dark) 100%);
  }
  .card-front { left: 40px; }
  .card-back { left: 620px; }

  .brand {
    position: absolute;
    display: flex;
    align-items: center;
    gap: 12px;
    font-weight: 700;
    color: var(--accent-orange);
    letter-spacing: 1px;
    text-transform: uppercase;
    white-space: nowrap;
  }
  .brand-dot {
    border-radius: 50%;
    background: var(--accent-blue);
    flex: none;
  }
  .card-front .brand {
    left: 50%; top: 50%;
    transform: translate(-50%, -50%);
    font-size: 34px;
  }
  .card-front .brand-dot { width: 30px; height: 30px; }
  .card-back .brand {
    right: 28px; top: 34px;
    font-size: 17px;
    gap: 8px;
  }
  .card-back .brand-dot { width: 16px; height: 16px; }

  .holder {
    position: absolute;
    left: 48px; top: 120px;
    padding-left: 14px;
    border-left: 3px solid var(--accent-orange);
  }
  .holder-name { font-size: 19px; font-weight: 700; color: var(--text-light); }
  .holder-role { font-size: 15px; color: var(--text-muted); margin-top: 3px; }

  .contacts {
    position: absolute;
    left: 48px; top: 190px;
    list-style: none;
  }
  .contact-row {
    display: flex; align-items: center; gap: 10px;
    font-size: 14px; color: var(--text-muted);
    height: 24px;
  }
  .contact-icon { width: 18px; height: 18px; flex: none; }
  .address {
    position: absolute;
    left: 48px; right: 20px; bottom: 20px;
    display: flex; align-items: center; gap: 10px;
    font-size: 12.5px; color: var(--text-muted);
    white-space: nowrap;
  }
</style>
</head>
<body>

<section class="card card-front" aria-label="Card front">
  <div class="card-surface" role="img" aria-label="Brushed gunmetal finish"></div>
  <div class="brand"><span class="brand-dot"></span>Tallow Partners</div>
</section>

<section class="card card-back" aria-label="Card back">
  <div class="card-surface" role="img" aria-label="Brushed gunmetal finish"></div>
  <div class="brand"><span class="brand-dot"></span>Tallow Partners</div>

  <div class="holder">
    <p class="holder-name">Dorian Whitlock</p>
    <p class="holder-role">Managing Director</p>
  </div>

  <ul class="contacts">
    <li class="contact-row">
      <svg class="contact-icon" viewBox="0 0 18 18"><circle cx="9" cy="9" r="7.5" fill="none" stroke="var(--accent-orange)" stroke-width="2"/><path d="M6.5 5.5l1.5 1.5-1 1a5 5 0 0 0 3 3l1-1 1.5 1.5-1 1.2c-3 0-6-3-6-6z" fill="var(--accent-orange)"/></svg>
      (+244) 947 582 316
    </li>
    <li class="contact-row">
      <svg class="contact-icon" viewBox="0 0 18 18"><circle cx="9" cy="9" r="7.5" fill="none" stroke="var(--accent-orange)" stroke-width="2"/><rect x="5" y="6" width="8" height="6" fill="none" stroke="var(--accent-orange)" stroke-width="1.3"/><path d="M5 6l4 3.5L13 6" fill="none" stroke="var(--accent-orange)" stroke-width="1.3"/></svg>
      dorian.whitlock@tallow-p.example
    </li>
    <li class="contact-row">
      <svg class="contact-icon" viewBox="0 0 18 18"><circle cx="9" cy="9" r="7.5" fill="none" stroke="var(--accent-orange)" stroke-width="2"/><circle cx="9" cy="9" r="4" fill="none" stroke="var(--accent-orange)" stroke-width="1.2"/><path d="M5 9h8M9 5v8" stroke="var(--accent-orange)" stroke-width="1"/></svg>
      www.tallow-p. example
    </li>
  </ul>

  <p class="address">
    <svg class="contact-icon" viewBox="0 0 18 18"><circle cx="9" cy="9" r="7.5" fill="none" stroke="var(--accent-orange)" stroke-width="2"/><path d="M9 13.5l-3-4a3 3 0 1 1 6 0z" fill="var(--accent-orange)"/></svg>
    N ° 17/18 Rua Veloso - R / C 2B Direita - Bairro Mutamba - Luanda
  </p>
</section>

</body>
</html>
```